Coffeeshop menu for filter tip

We want to have a cannabis (coffeeshop) menu in the size 25mm wide x 60mm wide. Some examples attached.

it must have the following text:
Menu

WEED p/g
Oblivane €16
Cloudplum €14
Tide Runner €14
Quincefig €16
Mega Marsh €14
Grey Heron €14

HASH p/g
Tashar Amber €12
Pebble Frost€11
Lime Dunes €14
Ash Petal €10

Target Market(s)

tourist in Amsterdam

Requirements
Nice to have
• cannabis sign leaf
• No Cigarettes allowed symbol

```html
<!DOCTYPE html>
<html lang="en">
<head>
<meta charset="utf-8">
<title>Amsterdam Coffeeshop Menu</title>
<link rel="stylesheet" href="https://fonts.googleapis.com/css2?family=Bebas+Neue&family=Kaushan+Script&family=Alegreya+Sans:wght@400;500&display=swap">
<style>
  :root {
    --green: #11873f;
    --green-light: #1a9a4c;
    --green-frame: #129343;
    --yellow: #f8ef6b;
    --cream: #e8f3dc;
    --rule: #cfe6c6;
    --white: #ffffff;
    --leaf: #7cc242;
    --no-red: #d8262c;
  }
  * { margin: 0; padding: 0; box-sizing: border-box; }
  html, body {
    width: 1200px; height: 2875px; overflow: hidden;
    background: var(--white);
  }
  .menu-board {
    position: relative; width: 1200px; height: 2875px;
    font-family: "Alegreya Sans", sans-serif;
  }
  .board-frame { position: absolute; inset: 0; }
  .emblem { position: absolute; left: 419px; top: 105px; width: 362px; height: 362px; }
  .city {
    position: absolute; left: 0; width: 1200px; top: 470px;
    text-align: center; font-family: "Kaushan Script", cursive;
    font-size: 82px; color: var(--yellow); line-height: 1;
  }
  .title {
    position: absolute; left: 0; width: 1200px; top: 580px;
    text-align: center; font-family: "Bebas Neue", sans-serif;
    font-size: 250px; line-height: 0.85; color: var(--white);
    letter-spacing: 2px;
  }
  .section-head {
    position: absolute; left: 238px; width: 734px;
    display: flex; justify-content: space-between; align-items: baseline;
  }
  .section-name {
    font-family: "Kaushan Script", cursive; font-size: 150px;
    color: var(--yellow); line-height: 1;
  }
  .unit { font-size: 56px; color: var(--cream); width: 140px; margin-right: 10px; }
  .price-list { position: absolute; left: 238px; width: 734px; list-style: none; }
  .price-row {
    position: relative; height: 126px;
    display: flex; align-items: center; justify-content: space-between;
    padding: 0 0 4px 20px;
    font-size: 62px; color: var(--cream);
  }
  .price-row::after {
    content: ""; position: absolute; left: 0; right: 0; bottom: 0;
    height: 3px; background: var(--rule);
  }
  .price-row::before {
    content: ""; position: absolute; left: -3px; right: -3px; bottom: -3px;
    height: 9px;
    background:
      radial-gradient(circle, var(--rule) 4px, transparent 5px) left center / 9px 9px no-repeat,
      radial-gradient(circle, var(--rule) 4px, transparent 5px) right center / 9px 9px no-repeat;
  }
  .price { color: var(--yellow); width: 140px; margin-right: 10px; font-weight: 500; }
  .weed-head { top: 860px; }
  .weed-list { top: 1007px; }
  .hash-head { top: 1850px; }
  .hash-list { top: 2049px; }
  .house-rule {
    position: absolute; left: 0; width: 1200px; top: 2640px;
    display: flex; justify-content: center; align-items: center; gap: 20px;
    font-size: 48px; color: var(--white); letter-spacing: 1px;
  }
  .no-smoke-icon { width: 100px; height: 100px; }
</style>
</head>
<body>
<main class="menu-board">
  <svg class="board-frame" width="1200" height="2875" viewBox="0 0 1200 2875" aria-hidden="true">
    <defs>
      <radialGradient id="boardGlow" cx="600" cy="300" r="700" gradientUnits="userSpaceOnUse">
        <stop offset="0" stop-color="#1b9b4e"/>
        <stop offset="1" stop-color="#11873f"/>
      </radialGradient>
    </defs>
    <path d="M34,181 Q600,-151 1166,181 L1166,2648 Q600,3028 34,2648 Z"
          fill="none" stroke="var(--green-frame)" stroke-width="11"/>
    <path d="M72,210 Q600,-104 1128,210 L1128,2629 Q600,2971 72,2629 Z"
          fill="url(#boardGlow)"/>
  </svg>

  <svg class="emblem" viewBox="0 0 362 362">
    <circle cx="181" cy="181" r="181" fill="var(--white)"/>
    <circle cx="181" cy="181" r="162" fill="none" stroke="var(--green)" stroke-width="10"/>
    <circle cx="181" cy="181" r="118" fill="var(--leaf)" role="img" aria-label="Cannabis leaf emblem"/>
  </svg>

  <div class="city">Amsterdam</div>
  <h1 class="title">MENU</h1>

  <div class="section-head weed-head">
    <h2 class="section-name">Weed</h2>
    <span class="unit">p/g</span>
  </div>
  <ul class="price-list weed-list">
    <li class="price-row"><span class="item">Oblivane</span><span class="price">€16</span></li>
    <li class="price-row"><span class="item">Cloudplum</span><span class="price">€14</span></li>
    <li class="price-row"><span class="item">Tide Runner</span><span class="price">€14</span></li>
    <li class="price-row"><span class="item">Quincefig</span><span class="price">€16</span></li>
    <li class="price-row"><span class="item">Mega Marsh</span><span class="price">€14</span></li>
    <li class="price-row"><span class="item">Grey Heron</span><span class="price">€14</span></li>
  </ul>

  <div class="section-head hash-head">
    <h2 class="section-name">Hash</h2>
    <span class="unit">p/g</span>
  </div>
  <ul class="price-list hash-list">
    <li class="price-row"><span class="item">Tashar Amber</span><span class="price">€12</span></li>
    <li class="price-row"><span class="item">Pebble Frost</span><span class="price">€11</span></li>
    <li class="price-row"><span class="item">Lime Dunes</span><span class="price">€14</span></li>
    <li class="price-row"><span class="item">Ash Petal</span><span class="price">€10</span></li>
  </ul>

  <div class="house-rule">
    <svg class="no-smoke-icon" viewBox="0 0 100 100" aria-hidden="true">
      <circle cx="50" cy="50" r="46" fill="var(--white)"/>
      <rect x="20" y="50" width="52" height="11" fill="#9a9a9a"/>
      <rect x="72" y="50" width="9" height="11" fill="#e06a2a"/>
      <path d="M70,44 q-6,-8 2,-16" fill="none" stroke="#9a9a9a" stroke-width="3"/>
      <circle cx="50" cy="50" r="42" fill="none" stroke="var(--no-red)" stroke-width="8"/>
      <line x1="21" y1="21" x2="79" y2="79" stroke="var(--no-red)" stroke-width="8"/>
    </svg>
    <span>NO CIGARETTES</span>
  </div>
</main>
</body>
</html>
```